Business Card

Just need business logo with phone number on it. 0487 312 654
And the following on the bottom of the card.

"Your local plumbing experts".
and emblems for zelpa card, cheque and cash

```html
<!DOCTYPE html>
<html lang="en">
<head>
<meta charset="utf-8">
<title>Ridgeway Plumbing &amp; Drainage — Business Card</title>
<link href="https://fonts.googleapis.com/css2?family=Roboto:ital,wght@0,400;0,700;0,900;1,400&display=swap" rel="stylesheet">
<style>
  :root {
    --brand-red: #e8202a;
    --brand-blue: #1a8fd0;
    --ink-slate: #4a555b;
    --cash-green: #4caf50;
    --cash-light: #b9e3a8;
    --card-white: #ffffff;
    --backdrop: #e9e6e1;
  }
  * { margin: 0; padding: 0; box-sizing: border-box; }
  html, body {
    width: 1200px;
    height: 902px;
    overflow: hidden;
    background: var(--backdrop);
    font-family: "Roboto", Arial, sans-serif;
  }
  .card {
    position: absolute;
    left: 100px;
    top: 166px;
    width: 1000px;
    height: 571px;
    background: var(--card-white);
    border-radius: 26px;
    overflow: hidden;
    box-shadow: 0 10px 30px rgba(0,0,0,0.12);
  }
  .brand-name {
    position: absolute;
    top: 92px;
    left: 0;
    width: 100%;
    text-align: center;
    color: var(--brand-red);
    font-weight: 900;
    line-height: 1;
  }
  .brand-name .brand-primary {
    display: block;
    font-size: 86px;
    letter-spacing: 4px;
  }
  .brand-name .brand-secondary {
    display: block;
    margin-top: 14px;
    font-size: 27px;
    letter-spacing: 6px;
  }
  .phone {
    position: absolute;
    top: 313px;
    left: 0;
    width: 100%;
    text-align: center;
    font-size: 32px;
    font-weight: 700;
    color: var(--brand-blue);
    letter-spacing: 0.5px;
  }
  .phone .phone-label { color: var(--brand-red); }
  .payment-methods {
    position: absolute;
    top: 398px;
    left: 0;
    width: 100%;
    display: flex;
    justify-content: center;
    align-items: center;
    gap: 30px;
  }
  .payment-card {
    width: 84px;
    height: 54px;
    border: 2px solid #c9cdd0;
    background: var(--card-white);
    display: flex;
    align-items: center;
    justify-content: center;
    color: var(--brand-blue);
    font-weight: 700;
    font-size: 21px;
    letter-spacing: 1px;
  }
  .tagline {
    position: absolute;
    top: 480px;
    left: 0;
    width: 100%;
    text-align: center;
    font-size: 25px;
    font-style: italic;
    font-weight: 400;
    letter-spacing: 2px;
    color: var(--brand-blue);
  }
  .accent-band {
    position: absolute;
    left: 0;
    bottom: 0;
    width: 100%;
    height: 20px;
    display: flex;
  }
  .accent-band .band-red { flex: 1; background: var(--brand-red); }
  .accent-band .band-blue { flex: 1; background: var(--brand-blue); }
</style>
</head>
<body>
  <main class="card">
    <h1 class="brand-name">
      <span class="brand-primary">RIDGEWAY</span>
      <span class="brand-secondary">PLUMBING &amp; DRAINAGE</span>
    </h1>

    <p class="phone"><span class="phone-label">P:</span> 0487 312 654</p>

    <div class="payment-methods">
      <div class="payment-card">ZELPA</div>

      <svg class="icon-cash" width="70" height="70" viewBox="0 0 70 70" role="img" aria-label="Cash accepted">
        <circle cx="35" cy="35" r="34" fill="var(--ink-slate)"/>
        <g transform="rotate(-30 35 35)">
          <rect x="17" y="22" width="36" height="22" rx="2" fill="var(--cash-light)"/>
          <rect x="21" y="27" width="36" height="22" rx="2" fill="var(--cash-green)"/>
          <circle cx="39" cy="38" r="6" fill="var(--cash-light)"/>
        </g>
      </svg>

      <svg class="icon-cheque" width="94" height="70" viewBox="0 0 94 70" role="img" aria-label="Cheque accepted">
        <rect x="2" y="18" width="86" height="48" rx="6" fill="var(--ink-slate)"/>
        <rect x="8" y="24" width="74" height="36" rx="3" fill="#ffffff"/>
        <text x="20" y="51" font-family="Roboto, Arial, sans-serif" font-weight="700" font-size="22" fill="var(--brand-blue)" text-anchor="middle">$</text>
        <rect x="34" y="33" width="36" height="4" fill="var(--ink-slate)"/>
        <rect x="34" y="41" width="36" height="4" fill="var(--ink-slate)"/>
        <rect x="34" y="49" width="24" height="4" fill="var(--ink-slate)"/>
        <g transform="rotate(38 62 24)">
          <rect x="57" y="-8" width="10" height="34" rx="2" fill="var(--brand-blue)"/>
          <polygon points="57,26 67,26 62,36" fill="var(--ink-slate)"/>
        </g>
      </svg>
    </div>

    <p class="tagline">Your local plumbing experts</p>

    <div class="accent-band">
      <span class="band-red"></span>
      <span class="band-blue"></span>
    </div>
  </main>
</body>
</html>
```